Binder design for a veterinary clinic

We are seeking a talented designer to create a standout design for ring binders specifically for our veterinary clinic. These binders will be used to organize materials from our Continuing Professional Development (CPD) projects for colleagues and interns. The design should be clean, professional, and align with our brand guidelines. To give you a better understanding of our branding, we’ve included the design of our vehicles as a reference. As additional reference, please visit www.tierpraxora.at

Target Market(s)

veterinarians

Industry/Entity Type

Veterinary

Font styles to use
Sans Serif

Colors
0054AA
0677BA
7BADD7
CADEEF
E8F1F8
FFC000
F8CF3A
FAE287
FDF2CF
FEFAEE

Requirements
Must have
• Our Logo an a clean design
Should not have
• to much images

```html
<!DOCTYPE html>
<html lang="de">
<head>
<meta charset="utf-8">
<title>Tierpraxora – Ordner CPD</title>
<link href="https://fonts.googleapis.com/css2?family=Montserrat:wght@500;700&display=swap" rel="stylesheet">
<style>
  :root {
    --stage: #e6e6e6;
    --navy: #2c3f53;
    --navy-deep: #1f2c3a;
    --gold: #d9a024;
    --gold-light: #e6b53e;
    --white: #f2f2f0;
    --hole: #b9bcbf;
  }
  html, body {
    margin: 0;
    width: 1200px;
    height: 900px;
    overflow: hidden;
    background: var(--stage);
  }
  .binder {
    position: absolute;
    left: 240px;
    top: 110px;
    width: 720px;
    height: 680px;
    display: flex;
  }
  .binder__spine {
    position: relative;
    width: 160px;
    height: 680px;
    background: var(--white);
    overflow: hidden;
  }
  .binder__cover {
    position: relative;
    width: 560px;
    height: 680px;
  }
  .binder__cover svg, .binder__spine svg {
    display: block;
  }
  .brand {
    position: absolute;
    right: 40px;
    top: 38px;
    font-family: "Montserrat", sans-serif;
  }
  .brand__name {
    margin: 0;
    font-weight: 700;
    font-size: 30px;
    letter-spacing: -0.5px;
    color: #ffffff;
    line-height: 1.1;
  }
  .brand__tagline {
    margin: 4px 0 0 18px;
    font-weight: 500;
    font-size: 12.5px;
    color: var(--gold);
  }
</style>
</head>
<body>
  <div class="binder">
    <div class="binder__spine">
      <svg width="160" height="680" viewBox="0 0 160 680">
        <rect class="spine-edge-gold" x="0" y="0" width="10" height="680" fill="var(--gold)"/>
        <rect class="spine-edge-navy" x="10" y="0" width="22" height="680" fill="var(--navy-deep)"/>
        <rect class="spine-edge-white" x="32" y="0" width="14" height="680" fill="var(--white)"/>
        <rect class="spine-band" x="46" y="0" width="30" height="680" fill="var(--navy-deep)"/>
        <circle class="spine-finger-hole" cx="112" cy="590" r="26" fill="var(--navy-deep)" stroke="var(--hole)" stroke-width="7"/>
      </svg>
    </div>
    <div class="binder__cover">
      <svg width="560" height="680" viewBox="0 0 560 680">
        <defs>
          <clipPath id="cover-clip"><rect width="560" height="680"/></clipPath>
          <linearGradient id="dog-fill" x1="0" y1="0" x2="1" y2="1">
            <stop offset="0" stop-color="#ffffff"/>
            <stop offset="1" stop-color="#e9e9e6"/>
          </linearGradient>
          <linearGradient id="cat-fill" x1="0" y1="0" x2="0" y2="1">
            <stop offset="0" stop-color="var(--gold-light)"/>
            <stop offset="1" stop-color="var(--gold)"/>
          </linearGradient>
        </defs>
        <g clip-path="url(#cover-clip)">
          <rect class="cover-bg" width="560" height="680" fill="var(--navy)"/>
          <ellipse class="arc-gold" cx="60" cy="420" rx="380" ry="470" fill="none" stroke="var(--gold)" stroke-width="14"/>
          <ellipse class="arc-white" cx="60" cy="420" rx="352" ry="442" fill="none" stroke="#ffffff" stroke-width="30"/>
          <rect class="dog-area" role="img" aria-label="Illustration: weiße Hundesilhouette mit dunklen Konturlinien" x="0" y="110" width="180" height="500" rx="28" fill="url(#dog-fill)"/>
          <rect class="cat-area" role="img" aria-label="Illustration: goldene Silhouette einer sitzenden Katze" x="215" y="270" width="125" height="340" rx="24" fill="url(#cat-fill)"/>
        </g>
      </svg>
      <div class="brand">
        <p class="brand__name">Tierpraxora</p>
        <p class="brand__tagline">Fachklinik für Kleintiere</p>
      </div>
    </div>
  </div>
</body>
</html>
```